Basic Commercial & Residential Real Estate Web Site

I need a basic website for a new real estate company that deals with both residential and commercial sales. It must be clean and professional. We sell homes, office buildings, farms, and ranches. It should feel crisp and clean.
I need a main page with my logo and links to commercial, residential, farm and land searches with contact data forms. Also incorporated would be a mls property search (IDX) form. I am in Northern California and the current site I posted is at www.tlvarden.com. I need the functionality of the links and the supporting pages. I do not have all the copy ready because I did not know what to expect.
Updates

Project Deadline Extended
Reason: I apologize, I am extremely busy and you all need more data to do a good job. All the designs are great so far and it is extremely difficult to choose at this point. I haven't given you enough data. I haver now uploaded some relevent photos (not very good) and edited the brief. I am looking for what I call the Landing or main page with some functionality built in to other pages which I also need. Example if you click on "Commercial" it should go to a page that discusses our commercial dept.......

I would like to thank all the designers for all their hard work and efforts, I wish I could reward you all.

Thanks again for your creative and professional designs.

Edwin

Target Market(s)

Corporate Execs for the Commercial Buildings
Homeowners/Families for the Homes and Farms
Upper end people for the land to build estates

Industry/Entity Type

Real Estate

Font styles to use
Sans Serif

Requirements
Must have
• Our Logo should be prominent, pronounced
Need contact data or button
Functional Page that links to other data pages
Must Have a "search for properties" feature
Must say "Commercial and Residential Representation"
Pictures of Commercial Building and Nice Home (Tradtional not contemporary)
Nice to have
• Individual Buttons or links to "Commercial, Residential, Farm/Ranch, Land"
Contact Data displayed
button that says "Maple Crest"-next to button is Maple Crest Logo-see www.maplecrest.bz
Links to "Buyers and "Sellers"
Links to Facebook, twitter,.....etc
Should not have
• 20+ story commercial buildings or ultra modern. See uploaded files of typical buildings for commercial.

```html
<!DOCTYPE html>
<html lang="en">
<head>
<meta charset="utf-8">
<title>Properties by Varden</title>
<link href="https://fonts.googleapis.com/css2?family=Open+Sans:wght@300;400;600;700&display=swap" rel="stylesheet">
<style>
:root{
  --black:#000;
  --blue:#29a8e0;
  --text:#777;
  --panel:rgba(24,32,40,.8);
  --listing-bg:#f3f3f3;
  --line:#dcdcdc;
  --footer:#2b2b2b;
  --footer-text:#bdbdbd;
  --social-1:#2f4f8f;
  --social-2:#39a9e6;
  --social-3:#1587b8;
  --social-4:#f7941d;
}
*{margin:0;padding:0;box-sizing:border-box}
html,body{width:1006px;height:1200px;overflow:hidden}
body{font-family:"Open Sans",Arial,sans-serif;background:#fff;position:relative;color:var(--text)}
.abs{position:absolute}
.header{left:0;top:0;width:1006px;height:586px;background:var(--black)}
.brand{left:85px;top:20px;color:#fff;line-height:1}
.brand .small{display:block;font-size:15px;font-weight:600;letter-spacing:.3px;text-align:right;width:176px}
.brand .big{display:block;font-size:62px;font-weight:400;letter-spacing:1px;margin-top:-2px}
.nav{top:44px;left:499px;display:flex;align-items:center;font-size:13px;color:#fff}
.nav a{color:#fff;text-decoration:none;display:block;height:26px;line-height:26px;padding:0 10px;margin-right:12px}
.nav a.active{background:var(--blue)}
.nav a:last-child{margin-right:0}
.hero{left:83px;top:119px;width:840px;height:444px;
  background:
    radial-gradient(ellipse 34% 40% at 45% 62%,rgba(206,178,140,.95),rgba(206,178,140,0) 100%),
    linear-gradient(180deg,#4f86cc 0%,#8fb6e0 22%,#c7d8ea 38%,#b49a7a 52%,#8d6c50 66%,#5a8f2e 78%,#6aa534 100%)}
.arrow-left{left:95px;top:326px;width:28px;height:28px}
.tagline{left:108px;top:502px;width:543px;height:44px;background:rgba(0,0,0,.75);color:#fff;font-size:23px;font-weight:600;line-height:44px;text-align:center;letter-spacing:.3px}
.search{left:671px;top:137px;width:236px;height:409px;background:var(--panel);padding:0 18px}
.search h2{color:var(--blue);font-size:19px;font-weight:600;text-align:center;margin-top:17px;height:26px}
.field-label{display:block;color:#ccc;font-size:12px;margin-top:9px;height:16px}
.field{height:30px;background:#fff;border-radius:2px;color:#999;font-size:12px;line-height:30px;padding:0 11px;position:relative;margin-top:1px}
.field svg{position:absolute;right:10px;top:12px}
.search-btn{display:block;margin:16px auto 0;width:105px;height:30px;background:#d5d5d5;border-radius:2px;color:#222;font-size:13px;font-weight:600;line-height:30px;text-align:center}
.intro{left:103px;top:617px;width:800px;font-size:13.4px;line-height:21px;text-align:center;color:var(--text)}
.listings{left:83px;top:728px;width:840px;height:252px;background:var(--listing-bg);border-top:2px solid var(--line);border-bottom:2px solid var(--line)}
.listings h3{position:absolute;left:13px;top:17px;color:var(--blue);font-size:16px;font-weight:700}
.listings .next{position:absolute;right:16px;top:20px}
.card{top:780px;width:151px;height:184px;background:#fff;border:1px solid #ddd;text-align:center}
.card .photo{margin:8px auto 0;width:135px;height:107px}
.card .title{color:#222;font-size:12px;margin-top:8px;line-height:16px}
.card .place{font-size:12px;line-height:16px;color:#666}
.contact-band{left:0;top:1017px;width:1006px;height:97px;border-top:1px solid #e5e5e5;background:linear-gradient(180deg,#fff,#f0f0f0)}
.contact{top:1033px;font-size:11.5px;line-height:17.5px;color:#777}
.contact .name{color:var(--blue)}
.contact svg{position:absolute;left:-31px;top:4px}
.footer{left:0;top:1114px;width:1006px;height:86px;background:var(--footer)}
.footer-links{left:85px;top:1133px;font-size:11.5px;color:var(--footer-text)}
.footer-links span{margin:0 9px}
.copyright{left:85px;top:1164px;font-size:11.5px;color:var(--footer-text)}
.social{left:782px;top:1145px;display:flex;gap:12px}
.social span{width:26px;height:26px;border-radius:50%;display:block}
</style>
</head>
<body>
<div class="abs header"></div>
<div class="abs brand"><span class="small">PROPERTIES BY</span><span class="big">VARDEN</span></div>
<nav class="abs nav">
  <a class="active" href="#">HOME</a><a href="#">COMMERCIAL</a><a href="#">RESIDENTIAL</a><a href="#">FARM</a><a href="#">CONTACT</a>
</nav>

<div class="abs hero" role="img" aria-label="Photo of a traditional two-storey brick and stucco family home on a green lawn under a blue sky"></div>
<svg class="abs arrow-left" viewBox="0 0 28 28"><circle cx="14" cy="14" r="14" fill="#fff" opacity=".9"/><path d="M16 9l-5 5 5 5" fill="none" stroke="#999" stroke-width="1.5"/></svg>
<div class="abs tagline">COMMERCIAL &amp; RESIDENTIAL REPRESENTATION</div>

<form class="abs search">
  <h2>PROPERTY SEARCH</h2>
  <label class="field-label">Property Type</label>
  <div class="field">Residential<svg width="10" height="6"><path d="M0 0h10L5 6z" fill="#777"/></svg></div>
  <label class="field-label">Budget</label>
  <div class="field">$0-$10,000,000<svg width="10" height="6"><path d="M0 0h10L5 6z" fill="#777"/></svg></div>
  <label class="field-label">Location</label>
  <div class="field">City / Zip</div>
  <label class="field-label">Size</label>
  <div class="field">1200 sqr ft<svg width="10" height="6"><path d="M0 0h10L5 6z" fill="#777"/></svg></div>
  <label class="field-label">Time Frame</label>
  <div class="field">Future<svg width="10" height="6"><path d="M0 0h10L5 6z" fill="#777"/></svg></div>
  <span class="search-btn">SEARCH NOW</span>
</form>

<p class="abs intro">Curabitur aliquet auctor consectetur. Suspendisse pharetra imperdiet nulla quis auctor. Sed at urna eu diam fringilla mattis. Praesent ac metus id odio interdum ornare. Aenean pulvinar, elit a ornare ullamcorper, metus mauris suscipit nisi, id tincidunt risus lorem luctus sem. Nulla in dolor vel lacus lacinia consequat eu at nunc. Integer tristique pretium purus, non vehicula eros consequat eu. Donec sed felis eget leo ullamcorper porttitor.</p>

<section class="abs listings">
  <h3>LATEST LISTINGS</h3>
  <svg class="next" width="14" height="14" viewBox="0 0 14 14"><circle cx="7" cy="7" r="7" fill="#c8c8c8"/><path d="M5.5 4l3.5 3-3.5 3z" fill="#fff"/></svg>
</section>
<div class="abs card" style="left:95px"><div class="photo" role="img" aria-label="Bright modern living room interior" style="background:linear-gradient(180deg,#f0efed 0%,#dcd8d3 55%,#a08468 80%,#6e5641 100%)"></div><div class="title">Phasellus in diam</div><div class="place">Grand Cayman<br>Cayman Islands</div></div>
<div class="abs card" style="left:261px"><div class="photo" role="img" aria-label="Brick family home with arched entrance" style="background:linear-gradient(180deg,#8d8983 0%,#b0896a 40%,#c59c78 65%,#5f7f3b 88%,#f2f2f2 100%)"></div><div class="title">Phasellus in diam</div><div class="place">Grand Cayman<br>Cayman Islands</div></div>
<div class="abs card" style="left:428px"><div class="photo" role="img" aria-label="Yellow waterfront villa with palm trees" style="background:linear-gradient(180deg,#fafafa 0%,#e9b77a 35%,#e2c760 55%,#4d7c38 78%,#7ea4b4 100%)"></div><div class="title">Phasellus in diam</div><div class="place">Grand Cayman<br>Cayman Islands</div></div>
<div class="abs card" style="left:594px"><div class="photo" role="img" aria-label="Contemporary house with swimming pool" style="background:linear-gradient(180deg,#3d74bd 0%,#2e2e2e 30%,#bdb4a6 55%,#4aa9dc 75%,#2a8ccc 100%)"></div><div class="title">Phasellus in diam</div><div class="place">Grand Cayman<br>Cayman Islands</div></div>
<div class="abs card" style="left:760px"><div class="photo" role="img" aria-label="Sunny lounge with sofas and large windows" style="background:linear-gradient(180deg,#d8ddcf 0%,#ecebe4 45%,#c9b89a 70%,#5e4836 100%)"></div><div class="title">Phasellus in diam</div><div class="place">Grand Cayman<br>Cayman Islands</div></div>

<div class="abs contact-band"></div>
<div class="abs contact" style="left:183px">
  <svg width="19" height="22" viewBox="0 0 19 22"><rect x="1" y="1" width="17" height="20" fill="none" stroke="#999" stroke-width="2"/><path d="M7 1v9l2.5-2 2.5 2V1" fill="#999"/></svg>
  PROPERTIES BY VARDEN<br>18215 Maple Crest Drive<br>Oakridge, CA 96099<br>BRE#01000000
</div>
<div class="abs contact" style="left:445px">
  <svg width="19" height="22" viewBox="0 0 19 22"><rect x="1" y="1" width="17" height="20" fill="none" stroke="#999" stroke-width="2"/><path d="M7 1v9l2.5-2 2.5 2V1" fill="#999"/></svg>
  <span class="name">Nora T. Lindell</span><br>nora@tlvarden.com<br>(530) 555-0142<br>BRE#01000001
</div>
<div class="abs contact" style="left:699px">
  <svg width="19" height="22" viewBox="0 0 19 22"><rect x="1" y="1" width="17" height="20" fill="none" stroke="#999" stroke-width="2"/><path d="M7 1v9l2.5-2 2.5 2V1" fill="#999"/></svg>
  <span class="name">Edwin G.Tallow</span><br>&nbsp;Edwin@tlvarden.com<br>530.555.0178&nbsp; - &nbsp;707.555.0193<br>BRE#01000002
</div>

<footer class="abs footer"></footer>
<div class="abs footer-links">Home<span>|</span>Commercial<span>|</span>Residential<span>|</span>Farm<span>|</span>Contact</div>
<div class="abs copyright">Copyright &nbsp;©&nbsp; 2014 &nbsp; PROPERTIES BY VARDEN. &nbsp; All rights reserved.</div>
<div class="abs social" aria-label="Social links">
  <span style="background:var(--social-1)"></span><span style="background:var(--social-2)"></span><span style="background:var(--social-3)"></span><span style="background:var(--social-4)"></span>
</div>
</body>
</html>
```